Website for my photography business

I need a website for my photography business, Bram Kellet Photography. I need a website that has a landing page with a cover photo of each kind of photography I do. For example, Nature, Weddings, Portraits and Architecture. I want it so that when someone comes onto my website they have to choose which kind of photography page they want to visit. So if they click on the wedding photo it will open to a page with my wedding portfolio images and a contact me button. If they choose nature photography I want them to be redirected to an e-commerce section where they can purchase prints. Architecture and Portraits should open up to their respective portfolios with about me and contact info. I like this kind of format because I want people who come to my website for a specific type of photography to be able to be directed there easily without having to look at a mix of other kinds of photography. I will provide a few files to use as placeholders. I have already purchased the bramkelletphotography.example domain name. A Wix website would be great because I am most familiar with it but I am open to anything.

Industry/Entity Type

Photographer

Number of Pages Required

5+ page

Requirements
Must have
• Landing Page and e-commerce

```html
<!DOCTYPE html>
<html lang="en">
<head>
<meta charset="utf-8">
<title>Bram Kellet Photography</title>
<link rel="stylesheet" href="https://fonts.googleapis.com/css2?family=Raleway:wght@400;500&display=swap">
<style>
  :root {
    --ink: #2c3140;
    --accent: #3c4f7c;
    --footer: #3a4f78;
    --white: #ffffff;
    --page: #ffffff;
  }
  * { margin: 0; padding: 0; box-sizing: border-box; }
  html, body { width: 1200px; height: 2265px; overflow: hidden; background: var(--page); }
  body { position: relative; font-family: "Raleway", Arial, sans-serif; color: var(--ink); }

  .site-header { position: absolute; left: 0; top: 0; width: 1200px; height: 91px; background: var(--white); }
  .brand { position: absolute; left: 130px; top: 34px; font-size: 20px; font-weight: 400; color: var(--accent); letter-spacing: 0.3px; }
  .main-nav { position: absolute; top: 41px; left: 0; width: 1200px; font-size: 15px; }
  .main-nav a { position: absolute; color: var(--ink); text-decoration: none; white-space: nowrap; }
  .main-nav a.is-current { color: var(--accent); }

  .hero { position: absolute; left: 0; top: 91px; width: 1200px; height: 593px;
    background: linear-gradient(180deg, #c9b7cf 0%, #9d9ab8 28%, #5fb9c8 48%, #9a7a4c 66%, #6b5532 100%); }
  .hero-title { position: absolute; left: 0; top: 367px; width: 1200px; text-align: center;
    font-size: 40px; font-weight: 400; color: var(--white); letter-spacing: 0.5px; line-height: 46px; }

  .category { position: absolute; width: 389px; }
  .category-number { position: absolute; font-size: 14px; color: var(--accent); line-height: 16px; }
  .category-cover { position: absolute; left: 0; width: 389px; }
  .category-name { position: absolute; left: 0; width: 389px; text-align: center; font-size: 26px; font-weight: 400; line-height: 30px; }
  .category-link { position: absolute; left: 0; width: 389px; text-align: center; font-size: 15px; color: var(--accent); line-height: 18px; text-decoration: none; }

  .cover-nature { background: linear-gradient(180deg, #2c3a2c 0%, #4b5a40 45%, #c97a3a 62%, #eef2f6 85%); }
  .cover-weddings { background: radial-gradient(circle at 55% 50%, #1e2446 0%, #5b5d6a 35%, #a59a86 100%); }
  .cover-portraits { background: linear-gradient(135deg, #d8d8d8 0%, #8a8a8a 45%, #b8b8b8 70%, #5a5a5a 100%); }
  .cover-architecture { background: linear-gradient(180deg, #e7e9ec 0%, #a7715a 35%, #c9bfae 60%, #9b9a96 85%, #6f8c4a 100%); }

  .site-footer { position: absolute; left: 0; top: 2173px; width: 1200px; height: 92px; background: var(--footer); color: var(--white); }
  .copyright { position: absolute; left: 111px; top: 43px; font-size: 15px; line-height: 18px; }
  .social { position: absolute; top: 41px; width: 20px; height: 20px; }
</style>
</head>
<body>
  <header class="site-header">
    <div class="brand">Bram Kellet Photography</div>
    <nav class="main-nav">
      <a class="is-current" style="left:639px">HOME</a>
      <a style="left:723px">CATAGORIES</a>
      <a style="left:854px">PORTFOLIO</a>
      <a style="left:977px">BIO</a>
      <a style="left:1041px">STORE</a>
    </nav>
  </header>

  <section class="hero" role="img" aria-label="Photographer with camera on tripod by a turquoise mountain lake">
    <h1 class="hero-title">BRAM KELLET PHOTOGRAPHY</h1>
  </section>

  <main>
    <article class="category" style="left:146px;top:0">
      <span class="category-number" style="left:2px;top:907px">01</span>
      <div class="category-cover cover-nature" style="top:934px;height:402px" role="img" aria-label="Red fox sitting in snow among pine trees"></div>
      <h2 class="category-name" style="top:1353px">NATURE</h2>
      <a class="category-link" style="top:1392px">SEE MORE</a>
    </article>

    <article class="category" style="left:634px;top:0">
      <span class="category-number" style="left:2px;top:846px">02</span>
      <div class="category-cover cover-weddings" style="top:874px;height:490px" role="img" aria-label="Two wedding rings resting on granite stone"></div>
      <h2 class="category-name" style="top:1377px">WEDDINGS</h2>
      <a class="category-link" style="top:1417px">SEE MORE</a>
    </article>

    <article class="category" style="left:146px;top:0">
      <span class="category-number" style="left:2px;top:1460px">03</span>
      <div class="category-cover cover-portraits" style="top:1487px;height:491px" role="img" aria-label="Black and white study of folded arms"></div>
      <h2 class="category-name" style="top:1991px">PORTRAITS</h2>
      <a class="category-link" style="top:2030px">SEE MORE</a>
    </article>

    <article class="category" style="left:643px;top:0">
      <span class="category-number" style="left:2px;top:1521px">04</span>
      <div class="category-cover cover-architecture" style="top:1547px;height:403px" role="img" aria-label="Modern brick and stone campus building"></div>
      <h2 class="category-name" style="top:1966px">ARCHITECTURE</h2>
      <a class="category-link" style="top:2006px">SEE MORE</a>
    </article>
  </main>

  <footer class="site-footer">
    <p class="copyright">©2020 All Rights Reserved</p>
    <svg class="social" style="left:988px" viewBox="0 0 20 20" aria-label="Social link"><circle cx="10" cy="10" r="8" fill="none" stroke="#fff" stroke-width="2"/></svg>
    <svg class="social" style="left:1028px" viewBox="0 0 20 20" aria-label="Social link"><circle cx="10" cy="10" r="8" fill="none" stroke="#fff" stroke-width="2"/></svg>
    <svg class="social" style="left:1069px" viewBox="0 0 20 20" aria-label="Social link"><circle cx="10" cy="10" r="8" fill="none" stroke="#fff" stroke-width="2"/></svg>
  </footer>
</body>
</html>
```